LLC needs a business card design that emphasizes consulting and expert witness in upstream oil and g

I need a business card design for my company called Obena Consultative Service, LLC. My expertise is in oil and gas upstream operations management to optimize performance and also as an expert witness for law firms in oil and gas upstream operations litigation.
The final design should communicate knowledge and hands-on experience as well as trust. (Obena means rope or lasso. Perhaps "Obena" should be in the form of a rope.) I do not like the color green in any shade. My first preference would be some shade of blue.
Industry/Entity Type
Oil And Gas

```html
<!DOCTYPE html>
<html lang="en">
<head>
<meta charset="utf-8">
<title>Obena Consultative Service, LLC — Business Card</title>
<link rel="stylesheet" href="https://fonts.googleapis.com/css2?family=Lato:wght@400;700;900&family=Arimo:wght@400&display=swap">
<style>
  :root {
    --backdrop: #2b2d2f;
    --card-front: #f1f1f1;
    --card-back: #22a3f7;
    --brand-blue: #3aa6f0;
    --ink: #333333;
    --ink-dark: #2a2a2a;
    --divider: #b9b9b9;
    --back-mark: #4cb8fb;
  }
  * { margin: 0; padding: 0; box-sizing: border-box; }
  html, body { width: 1200px; height: 864px; overflow: hidden; }
  body { background: var(--backdrop); position: relative; font-family: "Lato", sans-serif; }

  .card { position: absolute; width: 518px; height: 305px; }
  .card--front { left: 341px; top: 96px; background: var(--card-front); }
  .card--back { left: 342px; top: 453px; background: var(--card-back); }

  .person { position: absolute; left: 46px; top: 46px; }
  .person__name { font-size: 26px; font-weight: 400; color: var(--brand-blue); line-height: 1; letter-spacing: 0.2px; }
  .person__role { font-size: 16px; color: var(--ink); line-height: 1; margin-top: 7px; }

  .contact { position: absolute; left: 46px; top: 162px; list-style: none; }
  .contact__label { font-family: "Arimo", sans-serif; font-size: 13px; color: var(--brand-blue); line-height: 18px; }
  .contact__value { font-family: "Arimo", sans-serif; font-size: 13.5px; color: var(--ink-dark); line-height: 18px; }

  .brand { position: absolute; left: 246px; top: 88px; display: flex; align-items: center; }
  .brand__dot { width: 62px; height: 62px; border-radius: 50%; background: var(--brand-blue); }
  .brand__divider { width: 1px; height: 86px; background: var(--divider); margin: 0 16px 0 10px; }
  .brand__text { display: flex; flex-direction: column; }
  .brand__name { font-size: 44px; font-weight: 900; color: var(--brand-blue); line-height: 1; letter-spacing: 0.5px; }
  .brand__tagline { font-size: 13px; font-weight: 700; color: var(--ink); line-height: 1; margin-top: 3px; }

  .back-mark { position: absolute; left: 0; right: 0; top: 0; bottom: 0; display: flex; align-items: center; justify-content: center;
    font-size: 72px; font-weight: 900; color: var(--back-mark); letter-spacing: 2px; }
</style>
</head>
<body>
  <section class="card card--front" aria-label="Business card front">
    <div class="person">
      <p class="person__name">Daniel Harrow</p>
      <p class="person__role">Managing Director</p>
    </div>

    <ul class="contact">
      <li class="contact__label">telephone</li>
      <li class="contact__value">044-123 456 789</li>
      <li class="contact__label">email</li>
      <li class="contact__value">info@webname.com</li>
      <li class="contact__label">address</li>
      <li class="contact__value">1234, adrress goes here, country</li>
    </ul>

    <div class="brand">
      <span class="brand__dot" aria-hidden="true"></span>
      <span class="brand__divider" aria-hidden="true"></span>
      <div class="brand__text">
        <span class="brand__name">OBENA</span>
        <span class="brand__tagline">Consultative Service, LLC</span>
      </div>
    </div>
  </section>

  <section class="card card--back" aria-label="Business card back">
    <div class="back-mark">OBENA</div>
  </section>
</body>
</html>
```